Real Estate Newsletter

I would like a template created for a monthly newsletter; ideally, two pages long, including my photo, logo and contact info. I need it to look professional and be very easy for me to drop text into.

Target Market(s)

Past/current clients

Industry/Entity Type

Real Estate Agent

Font styles to use
Serif

Requirements
Must have
• My contact info/photo and logo
• (206) 555-0173
• mkorvell@tlxhb.com
• www.MarenKorvell.com
Nice to have
• I need a template where I can easily drop contact. I need the template to look professional so I can print it and mail it to current and past clients.

```html
<!DOCTYPE html>
<html lang="en">
<head>
<meta charset="utf-8">
<title>Maren Korvell – Real Estate Newsletter</title>
<link rel="stylesheet" href="https://fonts.googleapis.com/css2?family=Libre+Baskerville:wght@400;700&display=swap">
<style>
  :root{
    --backdrop:#ffffff;
    --frame:#d5d6da;
    --page:#ffffff;
    --band:#c7cbe6;
    --navy:#2b3a8f;
    --ink:#1a1a1a;
    --rule-dark:#1f2452;
    --ring:#8e99d0;
  }
  *{margin:0;padding:0;box-sizing:border-box}
  html,body{width:1200px;height:1200px;overflow:hidden;background:var(--backdrop)}
  body{position:relative;font-family:"Libre Baskerville",Georgia,serif;color:var(--ink)}
  .frame{position:absolute;left:56px;top:50px;width:1103px;height:1102px;background:var(--frame)}
  .page{position:absolute;left:82px;top:76px;width:1052px;height:1050px;background:var(--page);
        box-shadow:2px 3px 3px rgba(0,0,0,.35)}
  .abs{position:absolute}
  .masthead{left:167px;top:76px;width:507px;height:230px}
  .brand-name{left:167px;top:168px;width:507px;text-align:center;font-size:32px;font-weight:400;color:var(--navy);letter-spacing:1px}
  .section-band{left:167px;width:507px;height:45px;background:var(--band);color:var(--navy);
        font-size:21px;letter-spacing:1.2px;text-align:center;line-height:45px}
  .band-market{top:328px}
  .band-info{top:802px}
  .body-copy{left:167px;width:507px;font-size:15px;line-height:19.6px;letter-spacing:1.9px;text-align:justify;hyphens:auto}
  .copy-market{top:391px}
  .copy-info{top:864px}
  .body-copy p+p{margin-top:19.6px}
  .divider{left:756px;top:301px;width:0;height:763px;border-left:2px dashed var(--navy)}
  .portrait{left:832px;top:112px;width:232px;height:232px}
  .rule{left:832px;width:252px;border-top:2px dashed var(--navy)}
  .side-heading{left:832px;width:252px;text-align:center;color:var(--navy);font-size:18px;letter-spacing:2.5px}
  .contact-line{left:822px;width:272px;text-align:center;color:var(--navy);font-size:14.5px;letter-spacing:1.3px;white-space:nowrap}
  .icon{left:958px;width:20px;height:20px;transform:translateX(-50%)}
  .date-line{left:832px;width:270px;color:var(--navy);font-size:14.4px;letter-spacing:1.1px;white-space:nowrap}
  .date-line sup{font-size:8px}
  .field{left:832px;width:252px;color:var(--navy);font-size:14.4px;letter-spacing:0.9px;display:flex}
  .field .label{width:116px;white-space:nowrap}
  .field .colon{width:12px}
  .field .fill{flex:1;overflow:hidden;white-space:nowrap;letter-spacing:1.5px}
</style>
</head>
<body>
  <div class="frame"></div>
  <div class="page"></div>

  <svg class="abs masthead" viewBox="0 0 507 230" aria-hidden="true">
    <polygon points="0,0 507,0 507,190 255,228 0,190" fill="var(--band)"/>
    <polyline points="11,192 255,228 499,192" fill="none" stroke="var(--rule-dark)" stroke-width="4"/>
  </svg>
  <div class="abs brand-name">Maren Korvell</div>

  <div class="abs section-band band-market">The Real Estate Market</div>
  <div class="abs body-copy copy-market">
    <p>Many buyers and sellers are left feeling overwhelmed with the process and where to even begin. My job is to explain and guide you through the entire real estate process, from the initial meeting through the closing. I will be available day in and out to answer any questions you may have and address any concerns. My goal is that you feel you have my undivided attention during this process. I've spent my entire life in Seattle- born and raised in the Greenlake area- and I currently reside in Shoreline, after recently relocating from Lake Forest Park. On the side, my husband and I rehab and manage our rental properties. This side hobby has given me a unique perspective on handling renovations, local rents, and the potential appreciation of properties.</p>
    <p>I love what I do and the people I get to work with. I would be honored to walk through this process with you.</p>
  </div>

  <div class="abs section-band band-info">Information</div>
  <div class="abs body-copy copy-info">
    <p>We're all familiar with the Valuestimate, available on Homevalia, but did you know that the algorithm used to generate your Valuestimate can't actually take into account your home's updates, condition, street conditions or curb appeal? The only way to truly find out what your home is worth is to have a quick market analysis done. With just a few answers below, I can send you a quick market analysis that will give you a general idea of what your home would sell for in today's market.</p>
  </div>

  <div class="abs divider"></div>

  <svg class="abs portrait" viewBox="0 0 232 232" role="img" aria-label="Portrait photo of the agent">
    <defs>
      <linearGradient id="portraitTone" x1="0" y1="0" x2="1" y2="1">
        <stop offset="0" stop-color="#f3f1ef"/>
        <stop offset="0.5" stop-color="#b58a70"/>
        <stop offset="1" stop-color="#e8e4e0"/>
      </linearGradient>
    </defs>
    <circle cx="116" cy="116" r="111" fill="url(#portraitTone)" stroke="var(--ring)" stroke-width="7"/>
  </svg>

  <div class="abs rule" style="top:365px"></div>
  <div class="abs side-heading" style="top:382px">CONTACT</div>
  <div class="abs rule" style="top:425px"></div>

  <svg class="abs icon" style="top:437px" viewBox="0 0 20 20" aria-hidden="true">
    <circle cx="10" cy="10" r="9" fill="#111"/>
    <path d="M6.5 5.5c1-.6 1.6.2 2 1.2.3.8-.2 1.2-.6 1.5.4 1.3 1.3 2.4 2.6 3.1.4-.4.9-.9 1.6-.5 1 .5 1.7 1.1 1 2-1 1.2-2.6 1-4.2-.2C6.8 11 5.3 7.3 6.5 5.5z" fill="#fff"/>
  </svg>
  <div class="abs contact-line" style="top:459px">(206) 555-0173</div>

  <svg class="abs icon" style="top:500px" viewBox="0 0 20 20" aria-hidden="true">
    <circle cx="10" cy="10" r="8.5" fill="#fff" stroke="#111" stroke-width="2"/>
    <rect x="5.5" y="6.8" width="9" height="6.4" fill="none" stroke="#111" stroke-width="1.3"/>
    <polyline points="5.5,6.8 10,10.5 14.5,6.8" fill="none" stroke="#111" stroke-width="1.3"/>
  </svg>
  <div class="abs contact-line" style="top:522px">mkorvell@tlxhb.com</div>

  <svg class="abs icon" style="top:561px" viewBox="0 0 20 20" aria-hidden="true">
    <circle cx="10" cy="10" r="8.5" fill="none" stroke="#111" stroke-width="2"/>
    <ellipse cx="10" cy="10" rx="3.8" ry="8.5" fill="none" stroke="#111" stroke-width="1.5"/>
    <line x1="1.5" y1="10" x2="18.5" y2="10" stroke="#111" stroke-width="1.5"/>
    <line x1="3" y1="6" x2="17" y2="6" stroke="#111" stroke-width="1.3"/>
    <line x1="3" y1="14" x2="17" y2="14" stroke="#111" stroke-width="1.3"/>
  </svg>
  <div class="abs contact-line" style="top:588px">www.MarenKorvell.com</div>

  <div class="abs rule" style="top:665px"></div>
  <div class="abs side-heading" style="top:683px">DATE</div>
  <div class="abs rule" style="top:726px"></div>
  <div class="abs date-line" style="top:748px">[example] 12<sup>th</sup> February 2018</div>

  <div class="abs rule" style="top:817px"></div>
  <div class="abs side-heading" style="top:835px">TO :</div>
  <div class="abs rule" style="top:877px"></div>

  <div class="abs field" style="top:899px"><span class="label">Client Name</span><span class="colon">:</span><span class="fill">..............................</span></div>
  <div class="abs field" style="top:935px"><span class="label">Phone</span><span class="colon">:</span><span class="fill">..............................</span></div>
  <div class="abs field" style="top:970px"><span class="label">Email</span><span class="colon">:</span><span class="fill">..............................</span></div>
  <div class="abs field" style="top:1005px"><span class="label">Address</span><span class="colon">:</span><span class="fill">..............................</span></div>
</body>
</html>
```